Social Media App Needs PPT Template

We need a PowerPoint template for a new social media company based in the DC area called "Bold Ledger." We provide an interactive digital platform for executives to share actionable advice. We would like to see designs that use our orange logo color as an accent, but are mainly grey, white, and black. The final design should communicate clean, chic, modern, and professional.

Target Market(s)

Executives

Industry/Entity Type

Information Technology

Font styles to use
Sans Serif

Colors
f78f20
fbe7d2
ffffff
000000
e8e8e8
757575

Requirements
Must have
• My project must have title page and many options for the body of the ppt (graphs, tables, etc). It also needs to be easy to modify. I must have someone who is experienced in creating powerpoint templates.
Nice to have
• It would be nice to have a very modern and clean design that includes the logo on every page, but still leaves a lot of room for the content of the slide
Should not have
• My design project should not look to busy.

```html
<!DOCTYPE html>
<html lang="en">
<head>
<meta charset="utf-8">
<title>Bold Ledger – Chart Slide</title>
<link href="https://fonts.googleapis.com/css2?family=Lato:wght@300;400&display=swap" rel="stylesheet">
<style>
  :root {
    --stage: #cbcbcb;
    --navy: #222b3a;
    --orange: #f3921f;
    --grey-area: #a3a4a8;
    --white: #ffffff;
    --body-text: #555555;
    --axis-text: #666666;
    --grid: #b5b5b5;
    --footer-rule: #5a6274;
  }
  html, body {
    margin: 0;
    padding: 0;
    width: 1200px;
    height: 960px;
    overflow: hidden;
    background: var(--stage);
    font-family: "Lato", sans-serif;
  }
  .page-label {
    position: absolute;
    top: 66px;
    left: 0;
    width: 1200px;
    text-align: center;
    color: var(--white);
    font-weight: 300;
    font-size: 32px;
    letter-spacing: 1px;
    margin: 0;
  }
  .slide {
    position: absolute;
    left: 120px;
    top: 143px;
    width: 958px;
    height: 718px;
    background: var(--white);
  }
  .sidebar {
    position: absolute;
    left: 0;
    top: 0;
    width: 170px;
    height: 718px;
    background: var(--navy);
  }
  .brand {
    position: absolute;
    left: 0;
    top: 104px;
    width: 170px;
    text-align: center;
    color: var(--white);
    font-size: 24px;
    font-weight: 400;
    margin: 0;
  }
  .brand-dot {
    display: block;
    width: 34px;
    height: 34px;
    border-radius: 50%;
    background: var(--orange);
    margin: 0 auto 14px;
  }
  .site-url {
    position: absolute;
    left: 19px;
    top: 675px;
    color: var(--white);
    font-size: 17px;
    font-weight: 400;
  }
  .slide-title {
    position: absolute;
    left: 204px;
    top: 97px;
    margin: 0;
    color: var(--orange);
    font-weight: 400;
    font-size: 40px;
  }
  .title-rule {
    position: absolute;
    left: 204px;
    top: 153px;
    width: 716px;
    height: 1px;
    background: var(--orange);
    opacity: 0.7;
  }
  .chart {
    position: absolute;
    left: 0;
    top: 0;
    width: 958px;
    height: 718px;
  }
  .chart text {
    font-family: "Lato", sans-serif;
    fill: var(--axis-text);
  }
  .body-copy {
    position: absolute;
    left: 200px;
    top: 484px;
    width: 723px;
    margin: 0;
    color: var(--body-text);
    font-size: 14.4px;
    line-height: 21.8px;
    text-align: justify;
  }
  .footer-rule {
    position: absolute;
    left: 802px;
    top: 664px;
    width: 124px;
    height: 1px;
    background: var(--footer-rule);
  }
  .page-number {
    position: absolute;
    right: 36px;
    top: 683px;
    color: var(--axis-text);
    font-size: 13px;
  }
</style>
</head>
<body>
  <p class="page-label">Page 5</p>

  <section class="slide">
    <aside class="sidebar">
      <p class="brand"><span class="brand-dot"></span>Bold Ledger</p>
      <span class="site-url">boldledger.com</span>
    </aside>

    <h1 class="slide-title">Title of the page</h1>
    <div class="title-rule"></div>

    <svg class="chart" viewBox="150 179 1198 898" role="img" aria-label="Area chart of three series across three categories">
      <g stroke="var(--grid)" stroke-width="1.2" stroke-dasharray="8 7">
        <line x1="432" y1="431" x2="1183" y2="431"/>
        <line x1="432" y1="481" x2="1183" y2="481"/>
        <line x1="432" y1="528" x2="1183" y2="528"/>
      </g>
      <polygon fill="var(--navy)" points="700,500 723,496 1183,451 1183,671 700,671"/>
      <polygon fill="var(--orange)" points="432,671 432,590 620,494 1090,545 1183,527 1183,671"/>
      <polygon fill="var(--grey-area)" points="432,671 432,590 708,537 945,570 1090,545 1183,527 1183,671"/>
      <line x1="432" y1="431" x2="432" y2="671" stroke="#999" stroke-width="1"/>
      <g font-size="17" text-anchor="end">
        <text x="417" y="440">5</text>
        <text x="417" y="490">4</text>
        <text x="417" y="535">3</text>
        <text x="417" y="585">2</text>
        <text x="417" y="631">1</text>
        <text x="417" y="681">0</text>
      </g>
      <g font-size="17" text-anchor="middle">
        <text x="474" y="704">Category 1</text>
        <text x="789" y="704">Category 2</text>
        <text x="1122" y="704">Category 3</text>
      </g>
      <rect x="1214" y="431" width="10" height="10" fill="var(--grey-area)"/>
      <rect x="1214" y="457" width="10" height="10" fill="var(--orange)"/>
      <rect x="1214" y="484" width="10" height="10" fill="var(--navy)"/>
      <g font-size="17">
        <text x="1229" y="443">Series 1</text>
        <text x="1229" y="469">Series 2</text>
        <text x="1229" y="496">Series 3</text>
      </g>
    </svg>

    <p class="body-copy">Duis autem vel eum iriure dolor in hendrerit in vulputate velit esse molestie consequat, vel illum dolore eu feugiat nulla facilisis at vero eros et accumsan et iusto odio dignissim qui blandit praesent luptatum zzril delenit augue duis dolore te feugait nulla facilisi. Nam liber tempor cum soluta nobis eleifend option congue nihil imperdiet doming id quod mazim placerat facer possim assum.</p>

    <div class="footer-rule"></div>
    <span class="page-number">Page 4</span>
  </section>
</body>
</html>
```